business card deign

Logo needs the following on it.
1. attached logo
2. Tagline - "From cold drinks to good times...we bring it all to you!"
3. Name- Dalton Pikes, Founder and CPO
4. Address - 412 E. Carver Avenue, Ste 2207, Tampa, FL. 33917
5. Phone - 555.318.4726

```html
<!DOCTYPE html>
<html lang="en">
<head>
<meta charset="UTF-8">
<title>Bramlet Business Card</title>
<link href="https://fonts.googleapis.com/css2?family=Montserrat:wght@400;600;700&display=swap" rel="stylesheet">
<style>
  :root {
    --backdrop: #161616;
    --card: #2c2c2c;
    --ink: #f3f3f3;
    --ink-soft: #e4e4e4;
  }
  * { margin: 0; padding: 0; box-sizing: border-box; }
  html, body {
    width: 1200px; height: 1059px; overflow: hidden;
    background: var(--backdrop);
    font-family: "Montserrat", sans-serif;
    color: var(--ink);
  }
  .card {
    position: absolute;
    width: 690px; height: 392px;
    background: var(--card);
    border-radius: 16px;
    box-shadow: 0 10px 24px rgba(0,0,0,0.55);
  }
  .card--front { left: 256px; top: 89px; }
  .card--back { left: 255px; top: 547px; }

  .brand {
    position: absolute; left: 0; right: 0;
    display: flex; flex-direction: column; align-items: center;
  }
  .brand__dot { border-radius: 50%; background: var(--ink); }
  .brand__name {
    font-weight: 600; letter-spacing: 0.32em; text-transform: uppercase;
    padding-left: 0.32em; line-height: 1;
  }
  .card--front .brand { top: 62px; }
  .card--front .brand__dot { width: 72px; height: 72px; margin-bottom: 40px; }
  .card--front .brand__name { font-size: 26px; }
  .card--back .brand { top: 100px; }
  .card--back .brand__dot { width: 96px; height: 96px; margin-bottom: 54px; }
  .card--back .brand__name { font-size: 38px; }

  .person {
    position: absolute; right: 372px; top: 250px; text-align: right;
  }
  .person__name { font-size: 22px; font-weight: 700; letter-spacing: 0.04em; line-height: 1.1; }
  .person__title { font-size: 14.5px; font-weight: 400; color: var(--ink-soft); margin-top: 4px; letter-spacing: 0.02em; }
  .divider {
    position: absolute; left: 342px; top: 251px;
    width: 1px; height: 41px; background: var(--ink-soft);
  }
  .contact {
    position: absolute; left: 366px; top: 248px;
    list-style: none; font-size: 15px; letter-spacing: 0.02em;
  }
  .contact__item { display: flex; align-items: center; height: 25px; }
  .contact__icon { width: 12px; height: 12px; margin-right: 8px; fill: var(--ink); }
  .address, .tagline {
    position: absolute; left: 0; right: 0; text-align: center;
    font-size: 15px; letter-spacing: 0.02em; color: var(--ink-soft);
  }
  .address { top: 332px; }
  .tagline { top: 339px; }
</style>
</head>
<body>
  <section class="card card--front">
    <div class="brand">
      <span class="brand__dot"></span>
      <span class="brand__name">Bramlet</span>
    </div>
    <div class="person">
      <p class="person__name">DALTON PIKES</p>
      <p class="person__title">Founder and CPO</p>
    </div>
    <span class="divider"></span>
    <ul class="contact">
      <li class="contact__item">
        <svg class="contact__icon" viewBox="0 0 24 24" aria-hidden="true"><path d="M6.6 10.8a15 15 0 0 0 6.6 6.6l2.2-2.2a1 1 0 0 1 1-.25 11.4 11.4 0 0 0 3.6.57 1 1 0 0 1 1 1V20a1 1 0 0 1-1 1A17 17 0 0 1 3 4a1 1 0 0 1 1-1h3.5a1 1 0 0 1 1 1c0 1.25.2 2.45.57 3.57a1 1 0 0 1-.25 1z"/></svg>
        555.318.4726
      </li>
      <li class="contact__item">
        <svg class="contact__icon" viewBox="0 0 24 24" aria-hidden="true"><path d="M2 9l10-7 10 7v12H2zm2.5 1.2L12 15l7.5-4.8L12 4.5z"/></svg>
        dalton@bramletco.com
      </li>
    </ul>
    <p class="address">412 E. Carver Avenue, Ste 2207, Tampa, FL. 33917</p>
  </section>

  <section class="card card--back">
    <div class="brand">
      <span class="brand__dot"></span>
      <span class="brand__name">Bramlet</span>
    </div>
    <p class="tagline">From cold drinks to good times...we bring it all to you!</p>
  </section>
</body>
</html>
```